American cannabis tech company business card design

Pavrel.com is seeking a modern, professional, and brand-aligned business card that represents our company and its core values: Mission, Story, Values, and Impact. As an innovative cannabis company, we want a business card that is not only visually appealing but also serves as a representation of who we are and what we stand for.

Project Scope: Design a double-sided business card that integrates our brand identity and core values. Incorporate our key brand elements, ensuring a sleek and contemporary aesthetic. Visually reflect our core values (Mission, Story, Values, Impact) in a way that is engaging yet professional.

Target Market(s)

Vendors, third parties,

Contact Information for Business Card

Contact details (name, title, email, phone, website, etc.)

Font styles to use
Other font styles liked:
• Caslon, Centra

Colors

Designer to choose colors to be used in the design.

Requirements
Must have
• Pavrel.com logo and branding A creative yet clean way to integrate our core values (Mission, Story, Values, Impact) Modern typography and a well-structured layout
Nice to have
• forest green, grey, white, black
Should not have
• references to marijuana, leafs, plants, or related product

```html
<!DOCTYPE html>
<html lang="en">
<head>
<meta charset="utf-8">
<title>Pavrel.com Business Card</title>
<link href="https://fonts.googleapis.com/css2?family=Montserrat:wght@400;600;800&display=swap" rel="stylesheet">
<style>
  :root {
    --forest: #1a3a1f;
    --forest-deep: #163319;
    --forest-soft: #24492a;
    --white: #ffffff;
    --paper: #f4f4f4;
    --ink: #1c1c1c;
    --stage: #2b2b2b;
  }
  * { margin: 0; padding: 0; box-sizing: border-box; }
  html, body { width: 1200px; height: 900px; overflow: hidden; }
  body {
    background: var(--stage);
    font-family: "Montserrat", sans-serif;
    display: flex;
    flex-direction: column;
    align-items: center;
    justify-content: center;
    gap: 40px;
  }
  .card {
    position: relative;
    width: 660px;
    height: 378px;
    border-radius: 26px;
    overflow: hidden;
  }
  .card-back { background: var(--forest-deep); }
  .card-back .wordmark {
    position: absolute;
    left: 0; right: 0;
    top: 120px;
    text-align: center;
    font-weight: 800;
    font-size: 118px;
    letter-spacing: -2px;
    color: var(--forest-soft);
    line-height: 1;
    padding-left: 60px;
  }
  .card-front { background: linear-gradient(160deg, var(--white), var(--paper)); }
  .card-front .wordmark {
    position: absolute;
    left: 0; right: 0;
    top: 52px;
    text-align: center;
    font-weight: 800;
    font-size: 104px;
    letter-spacing: -2px;
    color: var(--forest);
    line-height: 1;
    padding-left: 90px;
  }
  .info-band {
    position: absolute;
    left: 0; right: 0;
    top: 200px;
    height: 104px;
    background: var(--forest);
    display: flex;
    align-items: center;
    color: var(--white);
  }
  .identity {
    width: 290px;
    text-align: right;
    padding-right: 20px;
  }
  .identity .name { font-weight: 600; font-size: 25px; line-height: 1.1; }
  .identity .title { font-weight: 400; font-size: 15px; margin-top: 2px; opacity: .9; }
  .divider { width: 2px; height: 62px; background: var(--white); }
  .contacts {
    list-style: none;
    padding-left: 20px;
    font-size: 15px;
    line-height: 1.55;
  }
  .contacts li { display: flex; align-items: center; gap: 10px; }
  .contacts svg { width: 12px; height: 12px; fill: var(--white); }
  .address {
    position: absolute;
    left: 0; right: 0;
    top: 326px;
    text-align: center;
    font-size: 15px;
    color: var(--ink);
    padding-right: 40px;
  }
</style>
</head>
<body>
  <section class="card card-back">
    <div class="wordmark">PAVREL</div>
  </section>

  <section class="card card-front">
    <div class="wordmark">PAVREL</div>
    <div class="info-band">
      <div class="identity">
        <div class="name">Owen Harlow</div>
        <div class="title">Co-Founder &amp; CEO</div>
      </div>
      <div class="divider"></div>
      <ul class="contacts">
        <li>
          <svg viewBox="0 0 24 24" aria-hidden="true"><path d="M6.6 10.8a15 15 0 0 0 6.6 6.6l2.2-2.2c.3-.3.7-.4 1-.2 1.1.4 2.3.6 3.6.6.6 0 1 .4 1 1V20c0 .6-.4 1-1 1A17 17 0 0 1 3 4c0-.6.4-1 1-1h3.5c.6 0 1 .4 1 1 0 1.3.2 2.5.6 3.6.1.3 0 .7-.2 1z"/></svg>
          +1 405-555-0148
        </li>
        <li>
          <svg viewBox="0 0 24 24" aria-hidden="true"><path d="M2 5h20v14H2z M2 5l10 8 10-8" /></svg>
          team@pavrel.com
        </li>
        <li>
          <svg viewBox="0 0 24 24" aria-hidden="true"><circle cx="12" cy="12" r="10"/></svg>
          www.pavrel.com
        </li>
      </ul>
    </div>
    <div class="address">718 Birch Lane Dallas, TX 75204</div>
  </section>
</body>
</html>
```